Calderine Coffee Bag for Retail Desing

.Our name and logo represent two things about the identity of our brand Turquoise Blue which is the color of the Honduras flag and the Guacamaya Bird (Ara Macao) national bird of Honduras we want that our logo and our packing reflects the peace that you can find by brewing your coffee and also the quality of our product which comes from one of the greatest coffee beans in the world.

We are looking for a design for our coffee bag there are some elements that we need to incorporate into the bag and we are providing you with a word document with guidelines to do it

Target Market(s)

Specialty coffee consumers is the United States

Industry/Entity Type

Product

Logo Text

CALDERINE COFFEE

Colors

Designer to choose colors to be used in the design.

Requirements
Must have
• Logo / Name of Brand
• Please Check Guidelines on Word Document
Nice to have
• The bag will be sent to print and all details are customizable feel free to be creative
Should not have

```html
<!DOCTYPE html>
<html lang="en">
<head>
<meta charset="utf-8">
<title>Calderine Coffee – Retail Bag</title>
<link href="https://fonts.googleapis.com/css2?family=Josefin+Sans:wght@400;600;700&family=Oswald:wght@300;400&display=swap" rel="stylesheet">
<style>
  :root {
    --backdrop: #ececec;
    --bag-blue: #1f7fa8;
    --bag-blue-deep: #14506e;
    --bag-blue-light: #3a9cc4;
    --seal-red: #c8362a;
    --ink-white: #ffffff;
    --label-white: #fbfbfb;
    --label-ink: #2b3e6b;
    --accent-red: #d8312a;
  }
  * { margin: 0; padding: 0; box-sizing: border-box; }
  html, body {
    width: 1200px; height: 950px; overflow: hidden;
    background: var(--backdrop);
    font-family: "Josefin Sans", sans-serif;
  }
  .dieline {
    position: absolute; top: 35px; left: 325px;
    display: flex; height: 880px;
    box-shadow: 0 12px 30px rgba(0,0,0,.15);
  }
  .panel { position: relative; height: 100%; overflow: hidden; }
  .panel-artwork {
    position: absolute; inset: 0;
    background: linear-gradient(180deg,
      var(--seal-red) 0%, var(--seal-red) 4%,
      #8a4a5a 12%, var(--bag-blue-deep) 20%,
      var(--bag-blue) 45%, var(--bag-blue-light) 70%, var(--bag-blue) 100%);
  }
  .side-panel { width: 150px; border-right: 1px solid rgba(0,0,0,.18); }
  .front-panel { width: 400px; }

  .story-label {
    position: absolute; left: 20px; top: 312px;
    width: 110px; height: 432px;
    background: var(--label-white);
    border-radius: 4px;
    display: flex; flex-direction: column; align-items: center;
    padding: 16px 8px;
  }
  .label-sprig {
    width: 34px; height: 34px; border-radius: 50%;
    background: #d6dcea;
  }
  .origin-story {
    margin-top: 16px;
    font-family: "Oswald", sans-serif; font-weight: 300;
    font-size: 8.5px; line-height: 1.45;
    text-transform: uppercase; text-align: center;
    color: var(--label-ink);
  }
  .label-map {
    margin-top: auto; width: 70px; height: 50px;
    border-radius: 6px;
    background: linear-gradient(135deg, #e2e6ef, #c9d1e3);
  }

  .brand-mark {
    position: absolute; left: 292px; top: 392px;
    width: 44px; height: 44px;
    background: var(--accent-red);
  }
  .brand-lockup {
    position: absolute; left: 86px; top: 455px;
    width: 236px; height: 150px;
    border: 2px solid var(--ink-white);
    display: flex; flex-direction: column; align-items: center; justify-content: center;
    text-align: center; color: var(--ink-white);
  }
  .brand-kicker, .brand-origin {
    font-size: 8px; font-weight: 700; letter-spacing: .4px;
  }
  .brand-rule {
    width: 124px; height: 2px; margin: 6px auto;
    background: var(--accent-red);
  }
  .brand-name {
    font-size: 30px; font-weight: 400; line-height: 1.05;
    letter-spacing: .3px;
  }
  .roast-info {
    position: absolute; left: 0; right: 0; top: 668px;
    text-align: center; color: var(--ink-white);
  }
  .roast-level { font-size: 17px; font-weight: 700; letter-spacing: .6px; }
  .roast-notes {
    margin-top: 10px; font-size: 9px; font-weight: 700;
    line-height: 1.7; letter-spacing: .5px;
  }
  .net-weight {
    position: absolute; left: 0; right: 0; top: 815px;
    text-align: center; color: var(--ink-white);
    font-family: "Oswald", sans-serif; font-weight: 400;
    font-size: 11px; letter-spacing: .3px;
  }
</style>
</head>
<body>
  <main class="dieline">
    <section class="panel side-panel">
      <div class="panel-artwork" role="img" aria-label="Macaw feather pattern in turquoise blue fading to a red top seal"></div>
      <div class="story-label">
        <div class="label-sprig" role="img" aria-label="Coffee branch illustration"></div>
        <p class="origin-story">
          Honduras is<br>a country that<br>has cultivated<br>arabica-specialty<br>coffee for over<br>200 years. This<br>historic tradition<br>of coffee has been<br>maintained and<br>developed by<br>small farmers.<br>Most of the coffee<br>production is<br>exported to<br>Europe. Today<br>Honduras has<br>established its<br>position as one<br>of the top ten<br>worldwide coffee<br>producers.
        </p>
        <div class="label-map" role="img" aria-label="Map of Honduras with the growing region highlighted"></div>
      </div>
    </section>

    <section class="panel front-panel">
      <div class="panel-artwork" role="img" aria-label="Macaw feather pattern in turquoise blue fading to a red top seal"></div>
      <div class="brand-mark" aria-hidden="true"></div>
      <div class="brand-lockup">
        <p class="brand-kicker">100% HONDURAS COFFEE</p>
        <div class="brand-rule"></div>
        <h1 class="brand-name">CALDERINE<br>COFFEE</h1>
        <div class="brand-rule"></div>
        <p class="brand-origin">SINGLE ORIGIN</p>
      </div>
      <div class="roast-info">
        <p class="roast-level">MEDIUM DARK</p>
        <p class="roast-notes">SMALL BATCH ROASTED<br>FARM DIRECT TRADE</p>
      </div>
      <p class="net-weight">NET WEIGHT 16OZ (1LB 16OZ) • 453G</p>
    </section>
  </main>
</body>
</html>
```